Every Shelf Set Neatly or ESN Organized needs a business card design. ESN Organized is a professi

We need a business card design that is clean, sharp and conveys a sense of organization. I already have a logo.

Target Market(s)

Families (specifically mothers), small business owners, parents, seniors

Industry/Entity Type

Business

Contact Information for Business Card

My website is www.esnorganized-example.com and my Facebook page is http://www.sociallink-example.com/everyshelfsetneatly. The phone number is 418-552-7094 and I want to be listed as Lorna M. Pelham, Owner

Requirements
Must have
• My logo.

```html
<!DOCTYPE html>
<html lang="en">
<head>
<meta charset="UTF-8">
<title>Every Shelf Set Neatly – Business Card</title>
<link rel="stylesheet" href="https://fonts.googleapis.com/css2?family=Roboto:wght@400;700&display=swap">
<style>
  :root {
    --backdrop: #b9a57a;
    --card-dark: #0b0b0c;
    --card-light: #ffffff;
    --brand-blue: #1a7fd9;
    --ink: #1a1a1a;
    --paper-text: #ffffff;
  }
  * { margin: 0; padding: 0; box-sizing: border-box; }
  html, body {
    width: 1200px; height: 950px; overflow: hidden;
    background: var(--backdrop);
  }
  .stage { position: relative; width: 1200px; height: 950px; }
  .card {
    position: absolute; left: 250px; width: 700px; height: 400px;
    overflow: hidden;
    box-shadow: 0 10px 24px rgba(0,0,0,0.25);
  }
  .card--back { top: 60px; background: var(--card-dark); }
  .card--front { top: 490px; background: var(--card-light); }

  .wordmark {
    position: absolute; left: 0; right: 0;
    display: flex; align-items: center; justify-content: center; gap: 14px;
    font-family: "Roboto", sans-serif; font-weight: 400;
    font-size: 40px; line-height: 1; letter-spacing: 0;
  }
  .wordmark__mark { width: 16px; height: 16px; border-radius: 50%; background: var(--brand-blue); }
  .card--back .wordmark { top: 180px; color: var(--paper-text); }
  .card--front .wordmark { top: 96px; color: var(--ink); }

  .holder {
    position: absolute; top: 196px; left: 0; right: 0; text-align: center;
    font-family: "Roboto", sans-serif;
  }
  .holder__name {
    color: var(--brand-blue); font-weight: 700; font-size: 26px; letter-spacing: 1px;
  }
  .holder__role {
    margin-top: 6px; color: var(--ink); font-size: 15px; letter-spacing: 1px;
  }
  .social-square {
    position: absolute; top: 196px; right: 40px;
    width: 34px; height: 34px; background: var(--brand-blue);
  }
  .contact-band {
    position: absolute; left: 0; right: 0; bottom: 0; height: 80px;
    background: var(--brand-blue);
    display: flex; align-items: center; gap: 36px; padding-left: 36px;
    font-family: "Roboto", sans-serif; font-size: 18px; color: var(--paper-text);
  }
  .contact-item { display: flex; align-items: center; gap: 10px; }
  .contact-item svg { width: 18px; height: 18px; }
</style>
</head>
<body>
<main class="stage">
  <section class="card card--back" aria-label="Card back">
    <div class="wordmark"><span class="wordmark__mark"></span>Every Shelf Set Neatly</div>
  </section>

  <section class="card card--front" aria-label="Card front">
    <div class="wordmark"><span class="wordmark__mark"></span>Every Shelf Set Neatly</div>
    <div class="holder">
      <p class="holder__name">LORNA M. PELHAM</p>
      <p class="holder__role">OWNER</p>
    </div>
    <span class="social-square" aria-hidden="true"></span>
    <div class="contact-band">
      <span class="contact-item">
        <svg viewBox="0 0 24 24" aria-hidden="true"><path fill="#fff" d="M6.6 10.8a15 15 0 0 0 6.6 6.6l2.2-2.2c.3-.3.7-.4 1-.2 1.1.4 2.3.6 3.6.6.6 0 1 .4 1 1V20c0 .6-.4 1-1 1A17 17 0 0 1 3 4c0-.6.4-1 1-1h3.5c.6 0 1 .4 1 1 0 1.3.2 2.5.6 3.6.1.3 0 .7-.2 1z"/></svg>
        418-552-7094
      </span>
      <span class="contact-item">
        <svg viewBox="0 0 24 24" aria-hidden="true"><circle cx="12" cy="12" r="9" fill="none" stroke="#fff" stroke-width="2"/><path d="M3 12h18M12 3c3 3 3 15 0 18M12 3c-3 3-3 15 0 18" fill="none" stroke="#fff" stroke-width="1.6"/></svg>
        www.esnorganized-example.com
      </span>
    </div>
  </section>
</main>
</body>
</html>
```